"The Orginal LoopPeg's" needs a Package Design!! Everybody's got a LoopPeg, What's Yours?

I need eye popping packaging design!! My LoopPeg's are gonna be big! I'm a single mom I'm based in AZ, so this is big for me. The LoopPeg's keep towels off the floor & so much more!! Color cardboard insert background, bright yellow and Bright blue, like a caribbean blue, funky font for the Product Name. The Original, can be smaller and in an easy script. I have some pictures so you can get an concept and basic design ideas. There are no limits to their uses!! Please call me for any questions or direction.
Updates

I want to thank you all for participating, You each brought a different perspective and had some really good ideas. I will definitely us this service again! Thank you, Dolores Fitzwick

Target Market(s)

Mom's, woman, men, students you name it!!

Colors
fbee3e
0293ce

Requirements
Must have
• Clear pvc packaging so you can see the product and they have to hang over so you see how they are used. The look needs to draw people in to it!! Read my instructions on the downloaded pics and info and if you have questions please let me know. The towel and towel bar can be like a drawing not actual towel picture. On the reverse side is a list of ideas and my website. Other colors for lettering aside from the Caribbean blue for the word "LoopPeg's" is up to you, use your expertise.
Should not have
• The blue is not on the color wheel that is shown here.

```html
<!DOCTYPE html>
<html lang="en">
<head>
<meta charset="utf-8">
<title>The Orginal LoopPeg's – Package Card</title>
<link rel="stylesheet" href="https://fonts.googleapis.com/css2?family=Bangers&family=Fredoka:wght@500;600&family=Luckiest+Guy&family=Open+Sans:wght@600;700&display=swap">
<style>
  :root {
    --sun-yellow: #fbee3e;
    --sun-glow: #fff7a6;
    --caribbean: #0293ce;
    --caribbean-deep: #0a7fb8;
    --maroon: #8a1538;
    --signal-red: #e3172b;
    --white: #ffffff;
    --backdrop: #6b3d1c;
  }
  * { box-sizing: border-box; margin: 0; padding: 0; }
  html, body { width: 1200px; height: 796px; overflow: hidden; }
  body { background: var(--backdrop); position: relative; font-family: "Open Sans", sans-serif; }

  .card { position: absolute; background: var(--sun-yellow); }
  .card--front { left: 38px; top: 132px; width: 548px; height: 628px; }
  .card--back {
    left: 614px; top: 36px; width: 548px; height: 654px;
    background: radial-gradient(ellipse at 50% 55%, var(--sun-glow) 0%, var(--sun-yellow) 60%);
  }

  /* Front */
  .brand { position: absolute; left: 120px; top: 28px; display: flex; align-items: center; gap: 12px; }
  .brand__dot { width: 22px; height: 22px; border-radius: 50%; background: var(--caribbean); }
  .brand__name { font-family: "Bangers", cursive; font-size: 50px; color: var(--caribbean); letter-spacing: 1px; }

  .tagline-band {
    position: absolute; left: 0; top: 130px; width: 548px; height: 70px;
    background: var(--caribbean); border-top: 3px solid var(--white); border-bottom: 3px solid var(--white);
    color: var(--white); text-align: center; font-weight: 600; font-size: 18px; line-height: 28px; padding-top: 4px;
  }

  .product-window {
    position: absolute; left: 78px; top: 223px; width: 411px; height: 194px;
    background: var(--caribbean); border-radius: 12px; padding: 14px;
  }
  .product-window__view {
    width: 100%; height: 100%;
    background: linear-gradient(90deg, #2f86a8 0 27%, #8fd43a 27% 51%, #b02e5c 51% 77%, #ef2f73 77% 100%);
  }

  .slogan-box {
    position: absolute; left: 42px; top: 441px; width: 468px; height: 105px;
    background: var(--caribbean); border: 4px solid var(--white);
    font-family: "Bangers", cursive; font-size: 34px; line-height: 38px; letter-spacing: 1px;
    color: var(--white); text-align: center; padding-top: 12px; padding-right: 30px;
  }
  .count-badge {
    position: absolute; left: 432px; top: 480px; width: 98px; height: 98px; border-radius: 50%;
    background: var(--caribbean); border: 4px solid var(--white); color: var(--white);
    text-align: center; font-weight: 600; font-size: 10px; line-height: 16px; padding-top: 26px;
  }
  .count-badge strong { display: block; font-size: 11px; }
  .fine-print {
    position: absolute; left: 0; top: 557px; width: 548px; padding-right: 84px; text-align: center;
    color: var(--maroon); font-size: 13px; font-weight: 600;
  }

  /* Back */
  .invite {
    position: absolute; left: 0; top: 58px; width: 548px; text-align: center;
    font-family: "Luckiest Guy", cursive; color: var(--caribbean); font-size: 16px; line-height: 22px; letter-spacing: 0.5px;
  }
  .invite__lead { color: var(--signal-red); font-size: 21px; }
  .invite__free { color: var(--signal-red); font-size: 20px; }

  .use-gallery { position: absolute; left: 38px; top: 134px; display: flex; gap: 9px; }
  .use-gallery__frame {
    width: 112px; height: 125px; background: var(--caribbean); border-radius: 10px; padding: 8px;
  }
  .use-gallery__frame > div { width: 100%; height: 100%; border-radius: 4px; }
  .shot--bib { background: linear-gradient(#c9c2bd, #7fb7d6); }
  .shot--towel { background: linear-gradient(#f4f0ec, #c7344a); }
  .shot--wrap { background: linear-gradient(#f2ebe4, #b7d86e); }
  .shot--shade { background: linear-gradient(#6a4a32 0 35%, #a9cfe8 35%); }

  .uses { position: absolute; top: 276px; display: flex; flex-direction: column; gap: 0; list-style: none; }
  .uses--left { left: 58px; }
  .uses--right { left: 284px; }
  .uses li {
    font-family: "Fredoka", sans-serif; font-weight: 500; color: var(--caribbean);
    font-size: 15.5px; line-height: 21.2px; display: flex; align-items: center; gap: 7px;
  }
  .tick { width: 14px; height: 14px; flex: none; }

  .closing {
    position: absolute; left: 0; top: 545px; width: 548px; text-align: center;
    font-family: "Luckiest Guy", cursive; color: var(--signal-red); font-size: 22px; letter-spacing: 1px;
  }
  .site { position: absolute; left: 0; top: 580px; width: 548px; text-align: center; color: var(--signal-red); font-size: 13px; font-weight: 700; }
</style>
</head>
<body>
  <svg width="0" height="0" style="position:absolute">
    <symbol id="tick" viewBox="0 0 14 14">
      <rect x="0.5" y="0.5" width="13" height="13" fill="#ffffff" stroke="#0293ce"/>
      <path d="M3 7.5 L6 10.5 L11.5 3" fill="none" stroke="#0293ce" stroke-width="2.4" stroke-linecap="round" stroke-linejoin="round"/>
    </symbol>
  </svg>

  <section class="card card--front">
    <div class="brand">
      <span class="brand__dot"></span>
      <span class="brand__name">The Orginal LoopPeg's</span>
    </div>
    <div class="tagline-band">NO MORE TOWELS ON THE FLOOR<br>&amp; SO MUCH MORE!!!</div>
    <div class="product-window">
      <div class="product-window__view" role="img" aria-label="Four patterned fabric loop straps shown through the clear window"></div>
    </div>
    <div class="slogan-box">EVERYBODY'S GOT A LOOPPEG<br>WHAT'S YOURS?</div>
    <div class="count-badge"><strong>4 LOOPPEGS</strong>per box</div>
    <p class="fine-print">Thin clear rubber band to hold product in place.</p>
  </section>

  <section class="card card--back">
    <p class="invite">
      <span class="invite__lead">ENDLESS USES</span> - POST A PICTURE OF YOUR<br>
      LOOPPEG IDEA TO OUR WEBSITE AND YOU COULD WIN<br>
      A <span class="invite__free">FREE</span> PACKAGE OF LIMITED EDITION LOOPPEGS'!!
    </p>
    <div class="use-gallery">
      <div class="use-gallery__frame"><div class="shot--bib" role="img" aria-label="Toddler wearing a towel fastened as a bib"></div></div>
      <div class="use-gallery__frame"><div class="shot--towel" role="img" aria-label="Hand towel hanging from a bar by a loop"></div></div>
      <div class="use-gallery__frame"><div class="shot--wrap" role="img" aria-label="Green towel worn as a wrap"></div></div>
      <div class="use-gallery__frame"><div class="shot--shade" role="img" aria-label="Loop used as a pull-down on a window shade"></div></div>
    </div>
    <ul class="uses uses--left">
      <li><svg class="tick"><use href="#tick"/></svg>Baby Bibs</li>
      <li><svg class="tick"><use href="#tick"/></svg>Baby Strollers</li>
      <li><svg class="tick"><use href="#tick"/></svg>Hanging Bathing Suits</li>
      <li><svg class="tick"><use href="#tick"/></svg>By the Pool</li>
      <li><svg class="tick"><use href="#tick"/></svg>Pull downs for Shades</li>
      <li><svg class="tick"><use href="#tick"/></svg>Tarp Holders</li>
      <li><svg class="tick"><use href="#tick"/></svg>Camping</li>
      <li><svg class="tick"><use href="#tick"/></svg>Room Dividers</li>
      <li><svg class="tick"><use href="#tick"/></svg>College Dorms</li>
      <li><svg class="tick"><use href="#tick"/></svg>The Gym</li>
      <li><svg class="tick"><use href="#tick"/></svg>Photography Backdrops</li>
      <li><svg class="tick"><use href="#tick"/></svg>Traveling</li>
    </ul>
    <ul class="uses uses--right">
      <li><svg class="tick"><use href="#tick"/></svg>Towel wraps</li>
      <li><svg class="tick"><use href="#tick"/></svg>Pet Training</li>
      <li><svg class="tick"><use href="#tick"/></svg>Drying Lingerie</li>
      <li><svg class="tick"><use href="#tick"/></svg>Tablecloths</li>
      <li><svg class="tick"><use href="#tick"/></svg>Dishtowels</li>
      <li><svg class="tick"><use href="#tick"/></svg>The Garage</li>
      <li><svg class="tick"><use href="#tick"/></svg>Hanging Quilts</li>
      <li><svg class="tick"><use href="#tick"/></svg>To hold your pants closed</li>
      <li><svg class="tick"><use href="#tick"/></svg>Curtains (no sewing!)</li>
      <li><svg class="tick"><use href="#tick"/></svg>Valences (no sewing!)</li>
      <li><svg class="tick"><use href="#tick"/></svg>Drapes (no sewing!)</li>
      <li><svg class="tick"><use href="#tick"/></svg>Shower Curtains</li>
    </ul>
    <p class="closing">THE ONLY LIMIT IS YOUR IMAGINATION</p>
    <p class="site">The original LoopPegs'.com</p>
  </section>
</body>
</html>
```